Salon and Spa Distributor Business Card

Need a business card. We are are distributor in the salon and spa industry. We identify with natural beauty. Need a card with:
Company Name: Petal Quarry"
Title: "President & CEO"
Address
Company Phone number
email
website
Tag Line:" The Professional Salon Source"

Industry/Entity Type

Business

Contact Information for Business Card

Name: Dov Strommen
Title: "President & CEO"
Address: 31 Harlow Ln, Bexmoor, NJ 07813
Company Phone number: 800-463-5918
email: dovstrommen@petalquarry.example
website: www.petalquarry.example

Requirements
Should not have
• No black backgrounds

```html
<!DOCTYPE html>
<html lang="en">
<head>
<meta charset="utf-8">
<title>Petal Quarry — Business Card</title>
<link rel="stylesheet" href="https://fonts.googleapis.com/css2?family=Didact+Gothic&display=swap">
<style>
  :root {
    --page-bg: #ecebe8;
    --card-bg: #ffffff;
    --brand-green: #1f7a2c;
    --leaf-green: #3db33a;
    --text-grey: #4a4a4a;
    --shadow: rgba(0, 0, 0, 0.18);
  }
  * { margin: 0; padding: 0; box-sizing: border-box; }
  html, body {
    width: 1200px;
    height: 716px;
    overflow: hidden;
    background: var(--page-bg);
    font-family: "Didact Gothic", "Century Gothic", sans-serif;
  }
  .canvas {
    position: relative;
    width: 1200px;
    height: 716px;
  }
  .business-card {
    position: absolute;
    left: 180px;
    top: 118px;
    width: 840px;
    height: 480px;
    background: var(--card-bg);
    box-shadow: 0 10px 30px var(--shadow);
    overflow: hidden;
  }
  .identity {
    position: absolute;
    left: 92px;
    top: 62px;
  }
  .person-name {
    font-size: 34px;
    font-weight: 400;
    color: var(--brand-green);
    letter-spacing: 0.5px;
    line-height: 1;
  }
  .job-title {
    margin-top: 8px;
    font-size: 13px;
    color: var(--text-grey);
  }
  .contact-list {
    position: absolute;
    left: 60px;
    top: 250px;
    list-style: none;
  }
  .contact-item {
    display: flex;
    align-items: center;
    gap: 12px;
    height: 30px;
    font-size: 19px;
    color: var(--brand-green);
    white-space: nowrap;
  }
  .contact-icon {
    width: 16px;
    height: 16px;
    flex: none;
    fill: var(--brand-green);
  }
  .contact-icon .line {
    fill: none;
    stroke: var(--brand-green);
  }
  .brand-mark {
    position: absolute;
    right: 0;
    top: 0;
    width: 360px;
    height: 480px;
    display: flex;
    flex-direction: column;
    align-items: center;
    justify-content: center;
    background: radial-gradient(circle at 60% 50%, rgba(61, 179, 58, 0.10), rgba(61, 179, 58, 0) 70%);
  }
  .brand-lockup {
    display: flex;
    align-items: center;
    gap: 14px;
  }
  .mark-dot {
    width: 22px;
    height: 22px;
    border-radius: 50%;
    background: var(--leaf-green);
  }
  .mark-name {
    font-size: 38px;
    color: var(--leaf-green);
    line-height: 1;
  }
  .tagline {
    margin-top: 14px;
    font-size: 15px;
    letter-spacing: 1px;
    color: var(--text-grey);
  }
</style>
</head>
<body>
<main class="canvas">
  <section class="business-card" aria-label="Petal Quarry business card">
    <header class="identity">
      <h1 class="person-name">Dov Strommen</h1>
      <p class="job-title">President &amp; CEO</p>
    </header>

    <ul class="contact-list">
      <li class="contact-item phone">
        <svg class="contact-icon" viewBox="0 0 16 16" aria-hidden="true"><path d="M3.5 1.5l2.6 2.6-1.5 1.8c.9 2 2.5 3.6 4.5 4.5l1.8-1.5 2.6 2.6-1.7 2.3C6.8 13.4 2.6 9.2 1.2 3.2z"/></svg>
        <span>800-463-5918</span>
      </li>
      <li class="contact-item email">
        <svg class="contact-icon" viewBox="0 0 16 16" aria-hidden="true"><path d="M1 3h14v10H1z M2.4 4.2V12h11.2V4.2L8 8.6z M2.8 4l5.2 3.9L13.2 4z" fill-rule="evenodd"/></svg>
        <span>dovstrommen@petalquarry.example</span>
      </li>
      <li class="contact-item website">
        <svg class="contact-icon" viewBox="0 0 16 16" aria-hidden="true"><circle class="line" cx="8" cy="8" r="6.5" stroke-width="1.4"/><path class="line" d="M1.5 8h13M8 1.5c-2.5 3.5-2.5 9.5 0 13M8 1.5c2.5 3.5 2.5 9.5 0 13" stroke-width="1.2"/></svg>
        <span>www.petalquarry.example</span>
      </li>
      <li class="contact-item address">
        <span>31 Harlow Ln, Bexmoor, NJ 07813</span>
      </li>
    </ul>

    <div class="brand-mark" role="img" aria-label="Petal Quarry brand mark area">
      <div class="brand-lockup">
        <span class="mark-dot" aria-hidden="true"></span>
        <span class="mark-name">Petal Quarry</span>
      </div>
      <p class="tagline">The Professional Salon Source</p>
    </div>
  </section>
</main>
</body>
</html>
```